Velvet Lantern rebranding my business with a new business card

I have my new logo and now I need a refresher on my business cards. I really want something fun and fresh. I like black background or anything to make the color pop.
Logo
Name: Velvet Lantern
Contact Info as stated below:
Mira Pellow
555-013-4762
Logo
Name: Velvet Lantern
Mira Pellow
555-013-4762
fb.me/VelvetLanternbyMira
Instagram: @VelvetLanternbyMira

Industry/Entity Type

Business

Contact Information for Business Card

double-sided. Logo on one side. Contact info on the other.

Requirements
Must have
• Logo
• Name: Velvet Lantern
• Contact Info as stated below:
• Mira Pellow
• 555-013-4762
• fb.me/VelvetLanternbyMira
• fb.me/VelvetLanternbyMira

```html
<!DOCTYPE html>
<html lang="en">
<head>
<meta charset="utf-8">
<title>Velvet Lantern – Business Card</title>
<link rel="stylesheet" href="https://fonts.googleapis.com/css2?family=Roboto:wght@400;700&family=Roboto+Condensed:wght@700&display=swap">
<style>
  :root {
    --page-bg: #e8e5e0;
    --card-dark: #1b1c1e;
    --card-light: #f3f3f2;
    --text-light: #ffffff;
    --text-dark: #333335;
    --text-muted: #55575a;
    --accent-pink: #e88bb8;
    --accent-soft: #f4c3d9;
    --accent-teal: #6fd0c2;
    --accent-ring: #f2b8cf;
  }
  * { margin: 0; padding: 0; box-sizing: border-box; }
  html, body {
    width: 1200px; height: 960px; overflow: hidden;
    background: var(--page-bg);
    font-family: "Roboto", Arial, sans-serif;
  }
  .canvas { position: relative; width: 1200px; height: 960px; }

  .card {
    position: absolute;
    width: 600px; height: 342px;
    border-radius: 14px;
    overflow: hidden;
  }

  /* Back side: logo */
  .card--back { left: 322px; top: 108px; background: var(--card-dark); }
  .card--back .logo-dot {
    position: absolute; left: 418px; top: 122px;
    width: 96px; height: 96px; border-radius: 50%;
    background: var(--accent-pink);
  }
  .card--back .brand-name {
    position: absolute; left: 386px; top: 226px; width: 160px;
    font-family: "Roboto Condensed", "Roboto", sans-serif;
    font-weight: 700; font-size: 26px; line-height: 1.05;
    color: var(--accent-soft); text-align: center;
  }
  .card--back .website {
    position: absolute; right: 42px; top: 295px;
    font-size: 14px; color: var(--text-light); letter-spacing: 0.2px;
  }

  /* Front side: contact */
  .card--front { left: 320px; top: 493px; background: var(--card-light); }
  .badge {
    position: absolute; left: 33px; top: 33px;
    width: 144px; height: 144px; border-radius: 50%;
    background: #fff; border: 2px solid var(--accent-ring);
    display: flex; align-items: center; justify-content: center;
  }
  .badge .brand-name {
    font-family: "Roboto Condensed", "Roboto", sans-serif;
    font-weight: 700; font-size: 19px; line-height: 1.1;
    color: var(--text-dark); text-align: center;
  }
  .logo-disc {
    position: absolute; left: 350px; top: 22px;
    width: 170px; height: 170px; border-radius: 50%;
    background: var(--accent-pink);
  }
  .brand-mark {
    position: absolute; left: 290px; top: 204px; width: 290px;
    font-family: "Roboto Condensed", "Roboto", sans-serif;
    font-weight: 700; font-size: 44px; line-height: 1.02;
    color: var(--text-dark); text-align: center;
  }
  .contact { position: absolute; left: 32px; top: 214px; }
  .contact__name {
    font-family: "Roboto Condensed", "Roboto", sans-serif;
    font-weight: 700; font-size: 21px; color: var(--text-dark);
    margin-bottom: 10px; letter-spacing: 0.2px;
  }
  .contact__list { list-style: none; }
  .contact__item {
    display: flex; align-items: center; gap: 8px;
    font-size: 14.5px; color: var(--text-muted); height: 19.5px;
  }
  .contact__icon { width: 13px; height: 13px; flex: none; }
</style>
</head>
<body>
<main class="canvas">

  <section class="card card--back" aria-label="Card back">
    <div class="logo-dot" aria-hidden="true"></div>
    <p class="brand-name">Velvet Lantern</p>
    <p class="website">www.velvetlantern.com</p>
  </section>

  <section class="card card--front" aria-label="Card front">
    <div class="badge"><p class="brand-name">Velvet<br>Lantern</p></div>
    <div class="logo-disc" aria-hidden="true"></div>
    <p class="brand-mark">Velvet Lantern</p>

    <div class="contact">
      <h1 class="contact__name">MIRA PELLOW</h1>
      <ul class="contact__list">
        <li class="contact__item">
          <svg class="contact__icon" viewBox="0 0 16 16" aria-hidden="true"><path fill="#333" d="M3.6 1.2l2.2 2.6-1.3 1.8c.9 2 2.4 3.5 4.4 4.4l1.8-1.3 2.6 2.2-1.2 2.6C7 13.3 2.7 9 1 3.3z"/></svg>
          <span>555-013-4762</span>
        </li>
        <li class="contact__item">
          <svg class="contact__icon" viewBox="0 0 16 16" aria-hidden="true"><g fill="none" stroke="#333" stroke-width="1.6"><circle cx="8" cy="8" r="6.5"/><ellipse cx="8" cy="8" rx="2.8" ry="6.5"/><path d="M1.5 8h13"/></g></svg>
          <span>www.velvetlantern.com</span>
        </li>
        <li class="contact__item">
          <svg class="contact__icon" viewBox="0 0 16 16" aria-hidden="true"><rect x="1" y="1" width="14" height="14" rx="2" fill="#333"/></svg>
          <span>fb.me/VelvetLanternbyMira</span>
        </li>
        <li class="contact__item">
          <svg class="contact__icon" viewBox="0 0 16 16" aria-hidden="true"><circle cx="8" cy="8" r="6.5" fill="#333"/></svg>
          <span>@VelvetLanternbyMira</span>
        </li>
      </ul>
    </div>
  </section>

</main>
</body>
</html>
```